Kelvor Engineers: Why you should hire us keepsake

New design. Open to plastic cards. We are an engineering firm that designs cell phone towers and commercial buildings. Please check out our website www.kelvorstruct.com for more details. We want people to remember our card and for it to be useful if possible. We want the same look and feel on these cards to be translated to other marketing material we may need such as brochures.

Target Market(s)

Architects, Developers and Telecommunication Carriers

Industry/Entity Type

Engineering

Contact Information for Business Card

Card with our company colors, logo, and innovative design with elements related to our industry.

Font styles to use
Sans Serif

Colors
9bcb3c
abd036
0255a3

Requirements
Must have
• Sleek and hip design
Nice to have
• Bright lime green and navy coloring that pops with an innovative design.
Should not have
• A basic and boring design

```html
<!DOCTYPE html>
<html lang="en">
<head>
<meta charset="utf-8">
<title>Kelvor Engineers – Business Card</title>
<link rel="stylesheet" href="https://fonts.googleapis.com/css2?family=Roboto:wght@400;500;900&family=Roboto+Condensed:wght@500&display=swap">
<style>
  :root {
    --backdrop: #262626;
    --card-white: #f2f2f2;
    --navy: #062a57;
    --lime: #14f00c;
    --text-grey: #4a4a4a;
    --divider: #c9c9c9;
    --cities: #e8ecf2;
  }
  * { margin: 0; padding: 0; box-sizing: border-box; }
  html, body { width: 1200px; height: 960px; overflow: hidden; }
  body { background: var(--backdrop); position: relative; font-family: "Roboto", Arial, sans-serif; }

  .card { position: absolute; width: 600px; height: 343px; box-shadow: 0 3px 8px rgba(0,0,0,.55); }

  .card-front { left: 314px; top: 113px; background: var(--card-white); }
  .front-band { position: absolute; left: 0; right: 0; bottom: 0; height: 24px; background: var(--lime); border-top: 2px solid var(--navy); }
  .front-wordmark {
    position: absolute; left: 44px; top: 128px; width: 242px;
    font-family: "Roboto", Arial, sans-serif; font-weight: 900; font-size: 58px;
    line-height: 1; color: var(--lime); letter-spacing: -1px; text-align: center;
  }
  .front-divider { position: absolute; left: 304px; top: 109px; width: 1px; height: 128px; background: var(--divider); }
  .contact { position: absolute; left: 332px; top: 116px; }
  .contact-name {
    font-family: "Roboto Condensed", Arial, sans-serif; font-weight: 500;
    font-size: 21px; color: var(--lime); letter-spacing: .1px; margin-bottom: 11px;
  }
  .contact-list { list-style: none; }
  .contact-list li { display: flex; align-items: center; height: 19px; font-size: 14.5px; color: var(--text-grey); }
  .contact-list svg { width: 13px; height: 13px; margin-right: 10px; fill: var(--lime); flex: none; }

  .card-back { left: 311px; top: 472px; background: var(--navy); }
  .back-wordmark {
    position: absolute; left: 0; right: 0; top: 108px; text-align: center;
    font-family: "Roboto", Arial, sans-serif; font-weight: 900; font-size: 124px;
    line-height: 1; color: var(--lime); letter-spacing: -3px;
  }
  .tagline {
    position: absolute; left: 0; right: 0; top: 267px;
    display: flex; justify-content: center; align-items: center; gap: 3px;
    font-family: "Roboto", Arial, sans-serif; font-weight: 500; font-size: 15px; color: var(--lime);
  }
  .tagline::before, .tagline::after { content: ""; width: 30px; height: 1.5px; background: var(--cities); }
  .cities { position: absolute; left: 0; right: 0; top: 288px; text-align: center; font-size: 15px; color: var(--cities); letter-spacing: .4px; }
</style>
</head>
<body>
  <section class="card card-front" aria-label="Business card front">
    <div class="front-wordmark">KELVOR</div>
    <div class="front-divider"></div>
    <div class="contact">
      <div class="contact-name">DANA WHITFIELD MOREAU</div>
      <ul class="contact-list">
        <li><svg viewBox="0 0 24 24"><path d="M6.6 10.8a15.1 15.1 0 0 0 6.6 6.6l2.2-2.2a1 1 0 0 1 1-.25 11.4 11.4 0 0 0 3.6.57 1 1 0 0 1 1 1V20a1 1 0 0 1-1 1A17 17 0 0 1 3 4a1 1 0 0 1 1-1h3.5a1 1 0 0 1 1 1c0 1.25.2 2.45.57 3.57a1 1 0 0 1-.25 1z"/></svg>555.310.4820</li>
        <li><svg viewBox="0 0 24 24"><path d="M7 1h10a2 2 0 0 1 2 2v18a2 2 0 0 1-2 2H7a2 2 0 0 1-2-2V3a2 2 0 0 1 2-2zm0 3v14h10V4zm5 15.2a1.1 1.1 0 1 0 0 2.2 1.1 1.1 0 0 0 0-2.2z"/></svg>555.614.2907</li>
        <li><svg viewBox="0 0 24 24"><path d="M2 5h20v14H2zm2 2v.5l8 5 8-5V7l-8 5z"/></svg>dmoreau@kelvorstruct.com</li>
        <li><svg viewBox="0 0 24 24"><path d="M12 2a10 10 0 1 0 0 20 10 10 0 0 0 0-20zm-1 17.9A8 8 0 0 1 4.1 10L9 15v1a2 2 0 0 0 2 2zm6.9-2.5A2 2 0 0 0 16 16h-1v-3a1 1 0 0 0-1-1H8v-2h2a1 1 0 0 0 1-1V7h2a2 2 0 0 0 2-2v-.4a8 8 0 0 1 2.9 12.8z"/></svg>www.kelvorstruct.com</li>
      </ul>
    </div>
    <div class="front-band"></div>
  </section>

  <section class="card card-back" aria-label="Business card back">
    <div class="back-wordmark">KELVOR</div>
    <div class="tagline">MULTI-DISCIPLINE ENGINEERING</div>
    <div class="cities">Denver | Raleigh | Tulsa | Sacramento</div>
  </section>
</body>
</html>
```